Corvana Tongue Works, LLC

We need a business card that includes information about our business and conveys a reliable business that provides document translation services and interpreters for a variety of corporate and individual clients. We want to come across as professional, reliable, yet approachable. It should include the following on one side:

ESL / ENL Language Classes, Private Lessons, and Online Tutors
PLEXA Training and Testing
Translating & Interpreting Services
Contact us about Over-the-Phone Interpreting in over 200 languages
24/7/365
www.corvanatongue.example

The other side should include (555) 481-3062

Rhoda Pelling, President
482 Garnet Ave., Ste. 219
Indianapolis, IN 40917

Please add USA as part of the address. Also, please add rmpelling@corvanatongueworks.example as the e-mail address. Thank you.

Target Market(s)

Business professionals, their families, the international community

Industry/Entity Type

Business

Contact Information for Business Card

24/7/365
www.corvanatongue.example

(555) 481-3062

Rhoda Pelling, President
482 Garnet Ave., Ste. 219
Indianapolis, IN 40917
USA

Font styles to use
Sans Serif

Colors

Designer to choose colors to be used in the design.

Requirements
Must have
• See project description
• e-mail address and web address
• Phone number
Nice to have
• a globe
• physical address
Should not have
• Should not have the same color scheme as other agencies in our market in Indiana unless it is blue and black. No purple or yellow.

```html
<!DOCTYPE html>
<html lang="en">
<head>
<meta charset="utf-8">
<title>Corvana Tongue Works – Business Card</title>
<link rel="stylesheet" href="https://fonts.googleapis.com/css2?family=Lato:wght@400;700&display=swap">
<style>
  :root {
    --backdrop: #d1d2d4;
    --brand-blue: #2394d6;
    --map-tint: #4aa6de;
    --paper: #ffffff;
    --ink: #1d1d1d;
    --ink-soft: #333333;
  }
  * { margin: 0; padding: 0; box-sizing: border-box; }
  html, body {
    width: 1198px; height: 1200px; overflow: hidden;
    background: var(--backdrop);
    font-family: "Lato", sans-serif;
  }
  .canvas { position: relative; width: 1198px; height: 1200px; }
  .card { position: absolute; width: 657px; height: 375px; overflow: hidden; }

  /* Front */
  .card--front { left: 262px; top: 149px; background: var(--brand-blue); }
  .world-map {
    position: absolute; left: 26px; top: 31px; width: 600px; height: 308px;
    border-radius: 40px;
    background: radial-gradient(ellipse at center, var(--map-tint) 0%, rgba(74,166,222,0.35) 55%, rgba(35,148,214,0) 80%);
  }
  .front-mark {
    position: absolute; left: 178px; top: 86px; width: 128px; height: 128px;
    border: 4px solid var(--paper); border-radius: 50%;
  }
  .front-name {
    position: absolute; left: 314px; top: 94px;
    color: var(--paper); font-size: 34px; font-weight: 400; line-height: 39px;
  }
  .services {
    position: absolute; left: 0; right: 0; top: 238px;
    text-align: center; color: var(--paper);
    font-size: 12.5px; line-height: 15.6px; list-style: none;
  }

  /* Back */
  .card--back { left: 272px; top: 638px; background: var(--paper); }
  .back-mark {
    position: absolute; left: 75px; top: 139px; width: 96px; height: 96px;
    border-radius: 50%; background: var(--brand-blue);
  }
  .back-name {
    position: absolute; left: 176px; top: 144px;
    color: var(--ink); font-size: 25px; font-weight: 400; line-height: 29px;
  }
  .divider {
    position: absolute; left: 327px; top: 0; width: 2px; height: 100%;
    background: var(--brand-blue);
  }
  .person { position: absolute; left: 354px; top: 120px; }
  .person__name { color: var(--brand-blue); font-size: 23px; font-weight: 700; line-height: 28px; }
  .person__title { color: var(--ink-soft); font-size: 18px; font-weight: 400; line-height: 22px; margin-left: 3px; }
  .contact-icon { position: absolute; left: 320px; width: 16px; height: 16px; }
  .contact-line {
    position: absolute; left: 354px; color: var(--ink);
    font-size: 13px; line-height: 15.6px; white-space: nowrap;
  }
</style>
</head>
<body>
<main class="canvas">

  <section class="card card--front" aria-label="Card front">
    <div class="world-map" role="img" aria-label="Faint world map silhouette behind the brand name"></div>
    <div class="front-mark"></div>
    <p class="front-name">Corvana<br>Tongue<br>Works, LLC</p>
    <ul class="services">
      <li>ESL / ENL Language Classes, Private Lessons, and Online Tutors</li>
      <li>PLEXA Training and Testing</li>
      <li>Translating &amp; Interpreting Services</li>
      <li>Contact us about Over-the-Phone Interpreting in over 200 languages</li>
      <li>24/7/365</li>
    </ul>
  </section>

  <section class="card card--back" aria-label="Card back">
    <div class="back-mark"></div>
    <p class="back-name">Corvana<br>Tongue<br>Works, LLC</p>
    <div class="divider"></div>

    <div class="person">
      <p class="person__name">Rhoda Pelling</p>
      <p class="person__title">President</p>
    </div>

    <svg class="contact-icon" style="top:186px" viewBox="0 0 16 16" aria-hidden="true">
      <circle cx="8" cy="8" r="8" fill="var(--brand-blue)"/>
      <path d="M5.2 4.2l1.4-.2.8 2-1 .8a5 5 0 0 0 2.8 2.8l.8-1 2 .8-.2 1.4c-.1.5-.6.8-1.1.7A7 7 0 0 1 4.5 5.3c-.1-.5.2-1 .7-1.1z" fill="#fff"/>
    </svg>
    <p class="contact-line" style="top:193px">(555) 481-3062</p>

    <svg class="contact-icon" style="top:207px" viewBox="0 0 16 16" aria-hidden="true">
      <circle cx="8" cy="8" r="8" fill="var(--brand-blue)"/>
      <g fill="none" stroke="#fff" stroke-width="1.3" stroke-linecap="round">
        <path d="M7 9.2l-1.3 1.3a1.4 1.4 0 0 1-2-2L5 7.2"/>
        <path d="M9 6.8l1.3-1.3a1.4 1.4 0 0 1 2 2L11 8.8"/>
        <path d="M6.5 9.5l3-3"/>
      </g>
    </svg>
    <p class="contact-line" style="top:213px">www.corvanatongue.example</p>

    <svg class="contact-icon" style="top:228px" viewBox="0 0 16 16" aria-hidden="true">
      <circle cx="8" cy="8" r="8" fill="var(--brand-blue)"/>
      <rect x="4" y="5.2" width="8" height="5.6" rx="0.6" fill="#fff"/>
      <path d="M4.3 5.6L8 8.4l3.7-2.8" fill="none" stroke="var(--brand-blue)" stroke-width="0.9"/>
    </svg>
    <p class="contact-line" style="top:233px">rmpelling@corvanatongueworks.example</p>

    <svg class="contact-icon" style="top:249px" viewBox="0 0 16 16" aria-hidden="true">
      <circle cx="8" cy="8" r="8" fill="var(--brand-blue)"/>
      <path d="M8 3.5a3 3 0 0 1 3 3c0 2.2-3 5.8-3 5.8S5 8.7 5 6.5a3 3 0 0 1 3-3z" fill="#fff"/>
      <circle cx="8" cy="6.5" r="1.1" fill="var(--brand-blue)"/>
    </svg>
    <p class="contact-line" style="top:254px">482 Garnet Ave., Ste. 219<br>Indianapolis, IN 40917<br>USA</p>
  </section>

</main>
</body>
</html>
```